Street Sign Project - Attract Customers

We need a street sign designed to display out the front of the building. It design will need to be 1800mm wide x 900mm high. We need to show potential customers where we are inviting. Some of the attachments are for inspiration. The sign will be printed on a sheet of aluminum. if you have a good look at our web site which is www.tv-r.com.au you should get a good feeling about the company and what we do.

Target Market(s)

Construction companies, landscaping and civil earth moving companies who may drive past our business

Industry/Entity Type

Building

Font styles to use
Sans Serif

Colors
ffffff
3277b5
000000

Requirements
Must have
• Company logo must be the main focus point
• The number "38" on the sign to show street number (300mm high)
• phone number - (02) 9413 5860
• web address - www.tv-r.com.au
• I have loaded pictures i would like to see used in the sign
Nice to have
• Banner picture as attached
Should not have
• Bright colours. Please use our blue colour where possible

```html
<!DOCTYPE html>
<html lang="en">
<head>
<meta charset="utf-8">
<title>TradeVale Rigging – Street Sign</title>
<link rel="stylesheet" href="https://fonts.googleapis.com/css2?family=Roboto+Condensed:wght@700&display=swap">
<style>
  :root {
    --sign-blue: #1f4fe6;
    --number-gold: #c99a1c;
    --number-white: #e8ebef;
    --text-white: #ffffff;
    --backdrop: #eef0f3;
    --photo-frame: #c9d3e6;
  }
  * { margin: 0; padding: 0; box-sizing: border-box; }
  html, body {
    width: 1200px; height: 847px; overflow: hidden;
    background: var(--backdrop);
    font-family: "Roboto Condensed", "Arial Narrow", sans-serif;
    font-weight: 700;
  }
  .street-sign {
    position: absolute; left: 50px; top: 148px;
    width: 1100px; height: 550px;
    background: var(--sign-blue);
    overflow: hidden;
  }
  .contact-line {
    position: absolute; left: 36px; top: 30px;
    display: flex; gap: 44px; align-items: baseline;
    color: var(--text-white);
  }
  .contact-phone { font-size: 36px; }
  .contact-web { font-size: 40px; }
  .service-photos {
    position: absolute; left: 36px; top: 104px;
    display: flex; gap: 12px;
  }
  .service-photo {
    width: 118px; height: 96px;
    border: 4px solid var(--photo-frame);
  }
  .photo-scaffold { background: linear-gradient(135deg, #8fa7b8, #dfe6e2); }
  .photo-hoist { background: linear-gradient(180deg, #6f8fb6, #c4cfdc); }
  .photo-roof { background: linear-gradient(160deg, #b8d0ea, #b24a3c 60%, #8a3a32); }
  .photo-site { background: linear-gradient(150deg, #d8dde2, #7b8a99); }
  .photo-conveyor { background: linear-gradient(135deg, #cfb89a, #e9ecef 55%, #6b86c9); }
  .company-name {
    position: absolute; left: 90px; top: 248px;
    color: var(--text-white);
    line-height: 1;
    text-transform: uppercase;
  }
  .company-name span { display: block; }
  .name-main { font-size: 100px; letter-spacing: 1px; }
  .name-second { font-size: 100px; margin-top: 8px; }
  .name-suffix { font-size: 34px; margin-top: 14px; letter-spacing: 3px; }
  .street-number-disc {
    position: absolute; left: 735px; top: -55px;
    width: 660px; height: 660px; border-radius: 50%;
    background: var(--number-gold);
  }
  .street-label {
    position: absolute; left: 780px; top: 40px; width: 290px;
    text-align: center;
    font-size: 56px; line-height: 1; color: var(--number-white);
  }
  .street-number {
    position: absolute; left: 780px; top: 112px; width: 290px;
    text-align: center;
    font-size: 270px; line-height: 1; letter-spacing: -4px;
    color: var(--number-white);
    transform: scaleY(1.4); transform-origin: top center;
  }
</style>
</head>
<body>
  <div class="street-sign">
    <div class="contact-line">
      <span class="contact-phone">(02) 9413 5860</span>
      <span class="contact-web">www.tv-r.com.au</span>
    </div>
    <div class="service-photos">
      <div class="service-photo photo-scaffold" role="img" aria-label="Photo of a scaffold hoist on a building site"></div>
      <div class="service-photo photo-hoist" role="img" aria-label="Photo of a tall material hoist against a building"></div>
      <div class="service-photo photo-roof" role="img" aria-label="Photo of a ladder hoist on a tiled roof"></div>
      <div class="service-photo photo-site" role="img" aria-label="Photo of a worker operating conveying equipment"></div>
      <div class="service-photo photo-conveyor" role="img" aria-label="Photo of boxes on a stair conveyor"></div>
    </div>
    <div class="company-name">
      <span class="name-main">TradeVale</span>
      <span class="name-second">Rigging</span>
      <span class="name-suffix">Pty Ltd</span>
    </div>
    <div class="street-number-disc"></div>
    <div class="street-label">St</div>
    <div class="street-number">38</div>
  </div>
</body>
</html>
```